In need of an AWESOME website for our Water Re-filling Store

The project is to design a website for our retail store front with the website www.quellbrookfillhouse.com. Currently if you go to that site it redirects you to our other site www.quellbrookbottleworks.com which is just our water bottle website. So, I need a new website created for www.quellbrookfillhouse.com (retail storefront)
Use our Squarespace to create a site with pages to help educate, tell about us, link to our water bottle brand site that is already created with Squarespace, and show the family and community aspects that we believe in. Our current water bottle website is www.quellbrookbottleworks.com for reference
We also sell hydration products, especially PRZQ products and have access to digital media through our PRZQ dealer site. we sell bottles, dispensers and other supplies for water refilling customers. We sell Ice as well.

Target Market(s)

Local residents looking to fill up their 1-5 gallon water jugs

Industry/Entity Type

Alkaline and Purified Water Retail Re-filling Store

Coding

Coded - Design and coding required

Font styles to use
Serif
Sans Serif

Colors
0054AA
0677BA
7BADD7
CADEEF
E8F1F8

Requirements
Must have
• pictures of our family in the about us section and pictures of our store inside and out.

```html
<!DOCTYPE html>
<html lang="en">
<head>
<meta charset="utf-8">
<title>Quellbrook Fill House</title>
<link href="https://fonts.googleapis.com/css2?family=Cormorant+Garamond:wght@500;600&family=Inter:wght@400;500;600&display=swap" rel="stylesheet">
<style>
:root{
  --blue:#0054AA;
  --blue-mid:#0677BA;
  --sky:#3aa3e0;
  --blue-soft:#7BADD7;
  --blue-pale:#CADEEF;
  --blue-mist:#E8F1F8;
  --navy:#0d1f5c;
  --navy-deep:#0a1745;
  --ink:#1a1f36;
  --muted:#5b6478;
  --white:#ffffff;
  --serif:'Cormorant Garamond', Georgia, serif;
  --sans:'Inter', Arial, sans-serif;
}
*{box-sizing:border-box;margin:0;padding:0}
html,body{width:1200px;height:4335px;overflow:hidden}
body{font-family:var(--sans);color:var(--ink);background:var(--white);position:relative}
section,header,footer{position:relative;width:1200px}
.abs{position:absolute}
.serif{font-family:var(--serif);font-weight:500}

/* buttons */
.btn{position:absolute;display:flex;align-items:center;gap:10px;height:42px;padding:0 8px 0 18px;border-radius:21px;font-size:15px;font-weight:500;white-space:nowrap}
.btn-dark{background:var(--navy);color:var(--white)}
.btn-light{background:var(--white);color:var(--ink)}
.btn-outline{border:1.5px solid var(--white);color:var(--white);padding-right:18px}
.btn .dot{width:24px;height:24px;border-radius:50%;display:flex;align-items:center;justify-content:center}
.btn-dark .dot{background:var(--white)}
.btn-light .dot{background:var(--navy)}

/* top */
.topbar{height:17px;background:var(--navy-deep);color:var(--white);font-size:10px;text-align:center;line-height:17px}
.nav{height:54px;background:var(--white)}
.nav-links{position:absolute;left:318px;top:0;height:54px;display:flex;align-items:center;gap:27px;font-size:12.5px;color:var(--ink)}
.nav .btn{right:100px;top:10px;height:34px;font-size:13px}
.brand-badge{position:absolute;left:100px;top:27px;width:106px;height:106px;border-radius:50%;background:var(--white);border:5px solid var(--blue);box-shadow:0 0 0 3px var(--white);z-index:5;display:flex;align-items:center;justify-content:center;text-align:center;color:var(--blue);font-family:var(--sans);font-weight:600;font-size:13px;line-height:1.2}

/* hero */
.hero{height:577px;background:linear-gradient(100deg,#1d1f5a 0%,#2b2c78 50%,#3f3f9e 100%);overflow:hidden}
.hero h1{position:absolute;left:99px;top:160px;font-family:var(--serif);font-weight:500;font-size:60px;line-height:62px;color:var(--white)}
.hero p{position:absolute;left:99px;top:298px;font-size:13px;color:#dfe3f5}
.hero-jugs{position:absolute;left:698px;top:180px;width:480px;height:397px;background:linear-gradient(180deg,#9fb6e8 0%,#6d8fd6 60%,#4e6fbf 100%);border-radius:30px 30px 0 0;opacity:.9}

/* products */
.products{height:666px;background:linear-gradient(180deg,#e6f0f8 0%,#d6e7f4 50%,#e9f2f9 100%)}
.section-title{font-family:var(--serif);font-weight:500;font-size:34px;color:var(--ink)}
.arrows{position:absolute;right:100px;top:66px;display:flex;gap:6px}
.arrow{width:26px;height:26px;border-radius:50%;border:1.5px solid var(--navy);display:flex;align-items:center;justify-content:center}
.arrow.filled{background:var(--navy)}
.card-row{position:absolute;left:99px;display:flex;gap:17px}
.card{width:322px}
.card .img{height:340px}
.card-foot{display:flex;justify-content:space-between;align-items:flex-start;padding:14px 0 14px;border-bottom:1px solid var(--blue-pale);font-size:16px;font-weight:500;line-height:22px}
.circ{width:26px;height:26px;border-radius:50%;border:1.5px solid var(--navy);display:flex;align-items:center;justify-content:center;flex:none}

/* about */
.about{height:528px}
.about-card{position:absolute;left:404px;top:88px;width:695px;height:365px;background:linear-gradient(100deg,#2e9be0,#55b4ec);border-radius:4px}
.ring{position:absolute;border-radius:50%;border:4px solid var(--sky);background:var(--white)}
.photo-circle{position:absolute;border-radius:50%}
.about h2,.visit h2{font-family:var(--serif);font-weight:500;font-size:34px;color:var(--white)}
.about p,.visit p{font-size:12.5px;line-height:23px;color:#e6f3fd}

/* features */
.features{height:346px}
.feature{position:absolute;top:0;width:300px;text-align:center}
.feature .icon{width:140px;height:140px;margin:0 auto;border-radius:50%;border:2px solid var(--blue-pale);display:flex;align-items:center;justify-content:center;box-shadow:0 0 0 6px var(--blue-mist)}
.feature h3{margin-top:22px;font-size:17px;font-weight:500}
.feature p{margin-top:10px;font-size:11px;line-height:17px;color:var(--muted)}
.vline{position:absolute;width:1px;background:#d7dde6}

/* aluminum */
.aluminum{height:432px;background:linear-gradient(90deg,#eaf3fa 0%,#eaf3fa 40%,#b9c4cf 62%,#6f7a86 100%)}
.aluminum h2{position:absolute;left:99px;top:44px;font-family:var(--serif);font-weight:500;font-size:34px}
.aluminum h4{position:absolute;left:99px;top:103px;font-size:16px;font-weight:500}
.aluminum p{position:absolute;left:99px;top:136px;width:510px;font-size:10.5px;line-height:17.5px;color:var(--muted)}
.stat{position:absolute;top:288px;width:150px;font-size:10.5px;line-height:17px;color:var(--ink)}
.stat .ic{width:42px;height:42px;border-radius:50%;border:1.5px solid var(--blue-pale);background:var(--white);display:flex;align-items:center;justify-content:center;margin-bottom:12px}

/* visit */
.visit{height:487px}
.visit-card{position:absolute;left:99px;top:86px;width:990px;height:332px;background:linear-gradient(100deg,#2e9be0,#55b4ec);border-radius:4px}

/* blog */
.blog{height:581px}
.blog .date{font-size:11px;color:var(--muted);margin-top:14px}
.blog .card-foot{padding-top:4px}

/* cta */
.cta{height:311px;background:linear-gradient(180deg,#ffffff 0%,#eaf3fa 35%,#9fcbec 75%,#5aa7df 100%);overflow:hidden}
.cta h2{position:absolute;left:0;top:22px;width:1200px;text-align:center;font-family:var(--serif);font-weight:500;font-size:60px;line-height:62px;color:var(--ink)}

/* footer */
.footer{height:330px;background:var(--navy-deep);color:var(--white)}
.footer h5{font-family:var(--serif);font-weight:500;font-size:18px}
.footer ul{list-style:none;font-size:12px;line-height:20px;color:#dfe4f2;margin-top:12px}
.footer .vl{position:absolute;top:38px;height:200px;width:1px;background:rgba(255,255,255,.15)}
.contact-row{display:flex;gap:10px;font-size:12px;line-height:18px;color:#dfe4f2;margin-top:12px}
.contact-row .ci{width:18px;height:18px;border-radius:50%;background:var(--white);flex:none;display:flex;align-items:center;justify-content:center}
.social{width:20px;height:20px;border-radius:50%;border:1.2px solid var(--white)}
.copy{position:absolute;left:0;top:276px;width:1200px;border-top:1px solid rgba(255,255,255,.15);padding-top:16px;text-align:center;font-size:11.5px;color:#dfe4f2}
</style>
</head>
<body>

<svg width="0" height="0" style="position:absolute">
  <defs>
    <symbol id="chev" viewBox="0 0 10 10"><path d="M3.5 1.5 7 5l-3.5 3.5" fill="none" stroke="currentColor" stroke-width="1.6" stroke-linecap="round" stroke-linejoin="round"/></symbol>
  </defs>
</svg>

<div class="topbar">Welcome to Quellbrook Fill House</div>

<header class="nav">
  <div class="brand-badge">Quellbrook<br>Fill House</div>
  <nav class="nav-links">
    <span>Home</span><span>Products</span><span>Water Refills</span><span>About Us</span><span>Our Store</span><span>Community</span><span>Contact</span>
  </nav>
  <span class="btn btn-dark">Refill Now <span class="dot"><svg width="10" height="10" style="color:var(--navy)"><use href="#chev"/></svg></span></span>
</header>

<section class="hero">
  <div class="hero-jugs" role="img" aria-label="Three large blue five-gallon refill water jugs"></div>
  <h1>Elevate Your Hydration.<br>Empower the Planet.</h1>
  <p>Your local source for premium water refills, hydration essentials, and everyday wellness.</p>
  <span class="btn btn-light" style="left:99px;top:414px">Refill Your Water Today <span class="dot"><svg width="10" height="10" style="color:#fff"><use href="#chev"/></svg></span></span>
  <span class="btn btn-outline" style="left:330px;top:414px">Shop Bottles &amp; Products</span>
</section>

<section class="products">
  <h2 class="section-title abs" style="left:99px;top:56px">Hydration That Goes Beyond the Refill</h2>
  <div class="arrows">
    <span class="arrow filled"><svg width="10" height="10" style="color:#fff;transform:scaleX(-1)"><use href="#chev"/></svg></span>
    <span class="arrow"><svg width="10" height="10" style="color:var(--navy)"><use href="#chev"/></svg></span>
  </div>
  <div class="card-row" style="top:121px">
    <div class="card">
      <div class="img" role="img" aria-label="Cold-pressed juice bottles on a refrigerated shelf" style="background:linear-gradient(180deg,#6b5a3c,#8a6a3a 50%,#a59a6a)"></div>
      <div class="card-foot"><span>PRZQ Electrolyte Drink Mixes</span><span class="circ"><svg width="10" height="10"><use href="#chev"/></svg></span></div>
    </div>
    <div class="card">
      <div class="img" role="img" aria-label="Cans of drink mixes displayed on a metal shelf" style="background:linear-gradient(180deg,#b7bcc4,#6d727c 60%,#3c404a)"></div>
      <div class="card-foot"><span>Reusable Water Bottles<br>&amp; Refill Containers</span><span class="circ"><svg width="10" height="10"><use href="#chev"/></svg></span></div>
    </div>
    <div class="card">
      <div class="img" role="img" aria-label="Store wall of water jugs, tumblers and dispensers" style="background:linear-gradient(180deg,#e9eef4,#7e8fa8 55%,#2a2f3a)"></div>
      <div class="card-foot"><span>Water Dispensers<br>&amp; Refill Accessories</span><span class="circ"><svg width="10" height="10"><use href="#chev"/></svg></span></div>
    </div>
  </div>
  <span class="btn btn-dark" style="left:486px;top:563px">Shop Bottles &amp; Products <span class="dot"><svg width="10" height="10" style="color:var(--navy)"><use href="#chev"/></svg></span></span>
</section>

<section class="about">
  <div class="about-card"></div>
  <svg class="abs" style="left:99px;top:40px" width="420" height="420"><path d="M210 4a206 206 0 0 0 0 412" fill="none" stroke="var(--sky)" stroke-width="4"/></svg>
  <div class="ring" style="left:106px;top:47px;width:406px;height:406px;border-color:var(--white)"></div>
  <div class="photo-circle" role="img" aria-label="Family of seven standing together on a beach at sunset" style="left:116px;top:57px;width:386px;height:386px;background:linear-gradient(180deg,#c9cfcf 0%,#b9b6a6 55%,#d8cdb5 100%)"></div>
  <h2 class="abs" style="left:522px;top:118px">A Purpose-Driven Bottled Water Brand</h2>
  <p class="abs" style="left:522px;top:174px;width:540px">At Quellbrook Bottleworks, hydration goes far beyond simply quenching thirst; it represents a deep commitment to enhancing both personal health and environmental sustainability. Drawing inspiration from the resilient and vibrant spirit of Tucson, AZ, the brand delivers a premium alkaline water experience thoughtfully designed to meet the needs of today's health-conscious and eco-aware consumers. Their cold-filled, ultra-purified alkaline water is carefully formulated to help neutralize body acidity, support optimal hydration, assist in natural detoxification processes, and promote sustained energy levels throughout the day.</p>
  <span class="btn btn-dark" style="left:511px;top:367px">Learn More About Us <span class="dot"><svg width="10" height="10" style="color:var(--navy)"><use href="#chev"/></svg></span></span>
</section>

<section class="features">
  <h2 class="section-title abs" style="left:0;top:-12px;width:1200px;text-align:center">Everything You Need to Stay Hydrated</h2>
  <div class="vline" style="left:446px;top:56px;height:240px"></div>
  <div class="vline" style="left:766px;top:56px;height:240px"></div>
  <div class="feature" style="left:136px;top:44px">
    <div class="icon"><svg width="40" height="62" viewBox="0 0 40 62"><rect x="9" y="2" width="22" height="9" fill="var(--navy)"/><rect x="4" y="13" width="32" height="47" rx="3" fill="var(--sky)"/><rect x="12" y="34" width="16" height="26" fill="#fff"/></svg></div>
    <h3>Water Refills</h3>
    <p>Clean, purified and alkaline water for<br>your everyday needs. Bring your own<br>containers or grab one in-store.</p>
  </div>
  <div class="feature" style="left:455px;top:44px">
    <div class="icon"><svg width="26" height="60" viewBox="0 0 26 60"><rect x="9" y="2" width="8" height="14" fill="var(--navy)"/><rect x="6" y="16" width="14" height="6" fill="var(--navy)"/><rect x="3" y="22" width="20" height="36" rx="5" fill="var(--sky)"/><path d="M13 32c-3 5-4 7-4 9a4 4 0 0 0 8 0c0-2-1-4-4-9z" fill="#fff"/></svg></div>
    <h3>Hydration Products</h3>
    <p>We carry trusted hydration solutions,<br>including electrolyte products like<br>PRZQ, to help you perform at your best.</p>
  </div>
  <div class="feature" style="left:779px;top:44px">
    <div class="icon"><svg width="36" height="66" viewBox="0 0 36 66"><rect x="11" y="2" width="14" height="8" rx="2" fill="var(--navy)"/><path d="M8 12h20l4 10v40a3 3 0 0 1-3 3H7a3 3 0 0 1-3-3V22z" fill="var(--sky)"/><rect x="4" y="24" width="28" height="14" fill="var(--navy)"/><rect x="4" y="44" width="28" height="5" fill="#fff" opacity=".6"/></svg></div>
    <h3>Bottles &amp; Dispensers</h3>
    <p>From 1–5 gallon containers to<br>dispensers and accessories—<br>we've got you covered.</p>
  </div>
</section>

<section class="aluminum">
  <div class="abs" role="img" aria-label="Close-up of brushed aluminum rods" style="left:560px;top:0;width:640px;height:432px;background:linear-gradient(90deg,rgba(234,243,250,0) 0%,rgba(150,160,172,.5) 40%,rgba(90,98,110,.7) 100%)"></div>
  <h2>Why Aluminum?</h2>
  <h4>It's the Future of Bottled Water.</h4>
  <p>Our bottles are designed to be refilled again and again — built for durability and made to go the distance with you. Whether you're rehydrating at the gym, on a hike, or between meetings, our aluminum bottles are your reusable hydration partner. And when it's finally time to part ways, aluminum doesn't go to waste — it goes to work. As the only packaging material that retains its value indefinitely, aluminum can be recycled infinitely without losing quality, making it the gold standard for circular, sustainable design. Every recycled bottle reduces the demand for new resources and lowers your environmental footprint, one responsible choice at a time.</p>
  <div class="stat" style="left:99px"><div class="ic"><svg width="22" height="22" viewBox="0 0 22 22" fill="none" stroke="var(--blue)" stroke-width="2"><path d="M11 3 6 11h5M16 8l2 6h-6M4 16h8"/></svg></div>75% of aluminum ever<br>made is still in use today.</div>
  <div class="vline" style="left:252px;top:290px;height:62px"></div>
  <div class="stat" style="left:270px"><div class="ic"><svg width="22" height="22" viewBox="0 0 22 22" fill="none" stroke="var(--blue)" stroke-width="2"><circle cx="11" cy="11" r="8"/><path d="M3 11h16M11 3c3 3 3 13 0 16M11 3c-3 3-3 13 0 16"/></svg></div>1 million plastic bottles<br>are used every minute.</div>
  <div class="vline" style="left:412px;top:290px;height:62px"></div>
  <div class="stat" style="left:430px"><div class="ic"><svg width="22" height="22" viewBox="0 0 22 22" fill="none" stroke="var(--blue)" stroke-width="2.2"><path d="M17 7a7 7 0 1 0 1 6"/><path d="M18 3v5h-5"/></svg></div>Aluminum is infinitely<br>recyclable – plastic is not.</div>
</section>

<section class="visit">
  <div class="visit-card"></div>
  <svg class="abs" style="left:710px;top:-2px" width="400" height="400"><path d="M200 4a196 196 0 0 1 0 392" fill="none" stroke="var(--sky)" stroke-width="4" transform="rotate(-40 200 200)"/></svg>
  <div class="ring" style="left:720px;top:8px;width:380px;height:380px;border-color:var(--white)"></div>
  <div class="photo-circle" role="img" aria-label="Storefront exterior with sign and glass entrance doors" style="left:731px;top:19px;width:358px;height:358px;background:linear-gradient(180deg,#9ec2e2 0%,#c9b89c 30%,#b59f80 60%,#3a3634 100%)"></div>
  <h2 class="abs" style="left:133px;top:120px">Experience Quellbrook Fill House</h2>
  <p class="abs" style="left:133px;top:170px;width:540px">From the moment you arrive, you'll notice a clean, organized, and welcoming environment built around your convenience. Our refill stations are designed for speed and ease, while our store layout makes it simple to find bottles, dispensers, and hydration products. Whether you're stopping by for a quick refill or browsing our products, we've created a space that feels comfortable, efficient, and community-focused.</p>
  <span class="btn btn-dark" style="left:121px;top:333px">Explore Our Store <span class="dot"><svg width="10" height="10" style="color:var(--navy)"><use href="#chev"/></svg></span></span>
</section>

<section class="blog">
  <h2 class="section-title abs" style="left:0;top:-2px;width:1200px;text-align:center">Quellbrook Wellness Blog</h2>
  <div class="card-row" style="top:45px">
    <div class="card">
      <div class="img" style="height:310px;background:linear-gradient(180deg,#d8d8d8,#8c8c8c 60%,#6f7a3a)" role="img" aria-label="Athlete holding a jar of pickles"></div>
      <div class="date">6/19/25</div>
      <div class="card-foot"><span>5 Hydration Hacks for Summer<br>Workouts</span><span class="circ"><svg width="10" height="10"><use href="#chev"/></svg></span></div>
    </div>
    <div class="card">
      <div class="img" style="height:310px;background:linear-gradient(180deg,#4f5d7a,#c99a6a 50%,#3a3328)" role="img" aria-label="Desert sunset with saguaro cactus"></div>
      <div class="date">6/19/25</div>
      <div class="card-foot"><span>Why Tucson Is Perfect for<br>Eco-Minded Living</span><span class="circ"><svg width="10" height="10"><use href="#chev"/></svg></span></div>
    </div>
    <div class="card">
      <div class="img" style="height:310px;background:linear-gradient(180deg,#3a3a3a,#1e1f22 60%,#2a2b2e)" role="img" aria-label="Two people lifting dumbbells in a dark gym"></div>
      <div class="date">6/19/25</div>
      <div class="card-foot"><span>How One Bottle Can Change a<br>Gym's Carbon Footprint</span><span class="circ"><svg width="10" height="10"><use href="#chev"/></svg></span></div>
    </div>
  </div>
  <span class="btn btn-dark" style="left:524px;top:480px">View All Blog <span class="dot"><svg width="10" height="10" style="color:var(--navy)"><use href="#chev"/></svg></span></span>
</section>

<section class="cta">
  <h2>Stop Paying More for Water.<br>Start Refilling Smarter.</h2>
  <span class="btn btn-dark" style="left:457px;top:168px">Get Direction <span class="dot"><svg width="10" height="10" style="color:var(--navy)"><use href="#chev"/></svg></span></span>
  <span class="btn btn-light" style="left:604px;top:168px">Contact Us <span class="dot"><svg width="10" height="10" style="color:#fff"><use href="#chev"/></svg></span></span>
</section>

<footer class="footer">
  <div class="abs" style="left:99px;top:48px;display:flex;align-items:center;gap:10px">
    <span style="width:26px;height:26px;border-radius:50%;border:2px solid var(--white)"></span>
    <span style="font-size:17px;font-weight:600;line-height:20px">Quellbrook<br>Fill House</span>
  </div>
  <p class="abs" style="left:99px;top:150px;width:310px;font-size:12px;line-height:19px;color:#dfe4f2">Family-owned hydration store providing premium alkaline and purified water, refill solutions, and hydration products for our local community.</p>
  <div class="abs" style="left:99px;top:222px;display:flex;gap:8px"><span class="social" aria-label="Instagram"></span><span class="social" aria-label="Facebook"></span></div>
  <div class="vl" style="left:468px"></div>
  <div class="vl" style="left:741px"></div>
  <div class="abs" style="left:560px;top:52px">
    <h5>Main Links</h5>
    <ul><li>Home</li><li>Products</li><li>Water Refills</li><li>About Us</li><li>Our Store</li><li>Community</li><li>Contact</li></ul>
  </div>
  <div class="abs" style="left:836px;top:52px;width:260px">
    <h5>Contact Us</h5>
    <div class="contact-row"><span class="ci"><svg width="10" height="10" viewBox="0 0 10 10"><path d="M2 1h2l1 2-1 1c.5 1 1 1.5 2 2l1-1 2 1v2c-4 .5-8-3.5-7-7z" fill="var(--navy)"/></svg></span>(520) 555-0148</div>
    <div class="contact-row" style="margin-top:16px"><span class="ci"><svg width="10" height="10" viewBox="0 0 10 10"><path d="M5 1a3 3 0 0 0-3 3c0 2 3 5 3 5s3-3 3-5a3 3 0 0 0-3-3z" fill="var(--navy)"/></svg></span>4127 N. Larkspur Rd., Ste. 210<br>Tucson, AZ 85741</div>
    <div class="contact-row" style="margin-top:16px"><span class="ci"><svg width="10" height="10" viewBox="0 0 10 10" fill="none" stroke="var(--navy)" stroke-width="1.4"><circle cx="5" cy="5" r="3.6"/><path d="M5 3v2l1.4 1"/></svg></span>Tuesday–Friday 9am–6pm<br>Saturday &amp; Sunday 10am–5pm<br>Closed on Mondays</div>
  </div>
  <div class="copy">© 2026 Quellbrook Fill House. All rights reserved. Clean Water. Better Hydration.</div>
</footer>

</body>
</html>
```